Business cards - BRENT Roofing & Siding

We need simple business cards made up for our Roofing & Siding business based in Calgary Alberta.
The logo on one side of the card and potentially our slogan "Built with trust, verified by time".
The other side could have:
-A small logo
-Rep name:
-Rep cell phone:
-Rep email:
-Office phone: 403-684-2093
-Website: PrairieShingleWorks.com

We would like to incorporate the colours from our logo, especially the lite blue on the jpeg file. I have attached the ai file and jpeg file. We like the colours better on the jpeg file.

I do not require a money back guarantee

```html
<!DOCTYPE html>
<html lang="en">
<head>
<meta charset="utf-8">
<title>BRENT Roofing &amp; Siding – Business Cards</title>
<link rel="stylesheet" href="https://fonts.googleapis.com/css2?family=Arimo:wght@400;700&display=swap">
<style>
  :root {
    --backdrop: #e4e4e2;
    --card-white: #ffffff;
    --brand-blue: #0f6bb8;
    --brand-blue-light: #3f86c8;
    --brand-blue-deep: #0a5aa0;
    --ink: #1a1a1a;
    --ink-soft: #555555;
    --accent-red: #e3161e;
    --rule: #8a8a8a;
  }
  * { box-sizing: border-box; margin: 0; padding: 0; }
  html, body { width: 1200px; height: 801px; overflow: hidden; }
  body {
    background: var(--backdrop);
    font-family: "Arimo", Arial, sans-serif;
    display: flex;
    align-items: center;
    justify-content: center;
    gap: 48px;
  }
  .card {
    width: 540px;
    height: 309px;
    position: relative;
    overflow: hidden;
    box-shadow: 0 10px 26px rgba(0,0,0,0.18);
  }

  /* Front: contact side */
  .card--front { background: var(--card-white); }
  .brand {
    position: absolute;
    left: 150px;
    top: 54px;
    width: 270px;
  }
  .brand__est {
    font-size: 13px;
    letter-spacing: 2px;
    color: var(--ink);
    margin-bottom: 6px;
    display: flex;
    align-items: center;
    gap: 8px;
  }
  .brand__mark {
    width: 14px; height: 14px;
    background: var(--brand-blue);
    display: inline-block;
  }
  .brand__name {
    font-weight: 700;
    color: var(--ink);
    line-height: 1;
  }
  .brand__name-main { display: block; font-size: 56px; letter-spacing: 4px; }
  .brand__name-sub { display: block; font-size: 17px; letter-spacing: 5px; margin-top: 8px; }

  .rep {
    position: absolute;
    left: 40px;
    top: 218px;
    width: 200px;
    text-align: right;
  }
  .rep__name {
    font-weight: 700;
    font-size: 17px;
    color: var(--accent-red);
    text-transform: uppercase;
  }
  .rep__title { font-size: 15px; color: var(--ink-soft); margin-top: 3px; }

  .divider {
    position: absolute;
    left: 258px;
    top: 196px;
    width: 1px;
    height: 84px;
    background: var(--rule);
  }

  .contacts {
    position: absolute;
    left: 276px;
    top: 190px;
    list-style: none;
  }
  .contacts__item {
    display: flex;
    align-items: center;
    gap: 9px;
    font-size: 15px;
    color: var(--ink-soft);
    height: 23px;
  }
  .contacts__icon { width: 13px; height: 13px; flex: none; }
  .contacts__icon * { fill: none; stroke: var(--accent-red); stroke-width: 2; }
  .contacts__icon .solid { fill: var(--accent-red); stroke: none; }

  /* Back: brand side */
  .card--back { background: var(--brand-blue); }
  .back__pattern {
    position: absolute;
    inset: 0;
    background:
      radial-gradient(ellipse at 25% 70%, var(--brand-blue-light) 0%, transparent 55%),
      linear-gradient(135deg, var(--brand-blue) 0%, var(--brand-blue-deep) 100%);
  }
  .back__brand {
    position: absolute;
    left: 0; right: 0;
    top: 92px;
    text-align: center;
    color: var(--card-white);
  }
  .back__est {
    font-size: 12px;
    letter-spacing: 2px;
    margin-bottom: 6px;
  }
  .back__name { font-weight: 700; line-height: 1; }
  .back__name-main { display: block; font-size: 58px; letter-spacing: 5px; }
  .back__name-sub { display: block; font-size: 17px; letter-spacing: 5px; margin-top: 8px; }
</style>
</head>
<body>

  <section class="card card--front" aria-label="Business card front">
    <div class="brand">
      <p class="brand__est"><span class="brand__mark"></span>Est. 1991</p>
      <p class="brand__name">
        <span class="brand__name-main">BRENT</span>
        <span class="brand__name-sub">ROOFING &amp; SIDING</span>
      </p>
    </div>

    <div class="rep">
      <p class="rep__name">Marcus Delaney</p>
      <p class="rep__title">Manager</p>
    </div>

    <div class="divider"></div>

    <ul class="contacts">
      <li class="contacts__item">
        <svg class="contacts__icon" viewBox="0 0 14 14" aria-hidden="true"><rect x="3" y="1" width="8" height="12" rx="1.5"/></svg>
        403-684-2093
      </li>
      <li class="contacts__item">
        <svg class="contacts__icon" viewBox="0 0 14 14" aria-hidden="true"><path class="solid" d="M3 1l3 3-1.5 1.5a8 8 0 0 0 4 4L10 8l3 3-2 2C6 13 1 8 1 3z"/></svg>
        403-684-2093
      </li>
      <li class="contacts__item">
        <svg class="contacts__icon" viewBox="0 0 14 14" aria-hidden="true"><rect class="solid" x="1" y="3" width="12" height="9"/><path d="M1 3l6 5 6-5" style="stroke:#fff;stroke-width:1.3"/></svg>
        info@PrairieShingleWorks.com
      </li>
      <li class="contacts__item">
        <svg class="contacts__icon" viewBox="0 0 14 14" aria-hidden="true"><circle class="solid" cx="7" cy="7" r="6"/><path d="M1 7h12M7 1c-3 3-3 9 0 12M7 1c3 3 3 9 0 12" style="stroke:#fff;stroke-width:1"/></svg>
        PrairieShingleWorks.com
      </li>
    </ul>
  </section>

  <section class="card card--back" aria-label="Business card back">
    <div class="back__pattern" role="img" aria-label="Embossed repeating roof pattern in shades of blue"></div>
    <div class="back__brand">
      <p class="back__est">Est. 1991</p>
      <p class="back__name">
        <span class="back__name-main">BRENT</span>
        <span class="back__name-sub">ROOFING &amp; SIDING</span>
      </p>
    </div>
  </section>

</body>
</html>
```